A clean crisp business card for a Landscape Construction company. Designed to be easy to read contact/ info and also be appealing/interesting, unlike a traditional business card.

Industry/Entity Type

Landscape Construction

Contact Information for Business Card

Company name : Brambleford Landscape Construction, phone number: (877) 62Vista, website:Bramblefordyards.example, Email, sales@bramblefordyards.example

Requirements
Nice to have
• Luxurious finishes/ details…. Icons or emblems next to contact info
Should not have
• Clipart or general pictures

```html
<!DOCTYPE html>
<html lang="en">
<head>
<meta charset="utf-8">
<title>Brambleford Landscape Construction – Business Card</title>
<link href="https://fonts.googleapis.com/css2?family=Cinzel:wght@600&family=Open+Sans:wght@400;600&display=swap" rel="stylesheet">
<style>
  :root {
    --backdrop: #e9e6e1;
    --card: #121212;
    --card-sheen: #2a2a2a;
    --leaf-green: #8fd13f;
    --gear-blue: #3f7fcf;
    --ink: #f2f2f2;
  }
  * { box-sizing: border-box; margin: 0; padding: 0; }
  html, body { width: 1200px; height: 913px; overflow: hidden; }
  body {
    background: var(--backdrop);
    position: relative;
    font-family: "Open Sans", Arial, sans-serif;
  }
  .card {
    position: absolute;
    width: 580px;
    height: 331px;
    background: linear-gradient(125deg, var(--card) 0%, var(--card) 35%, var(--card-sheen) 52%, var(--card) 70%);
    border-radius: 4px;
    box-shadow: 0 10px 28px rgba(0,0,0,.28);
    overflow: hidden;
  }
  .card--front { left: 60px; top: 90px; }
  .card--back { left: 560px; top: 490px; }

  .wordmark {
    position: absolute;
    display: flex;
    align-items: center;
    font-family: "Open Sans", Arial, sans-serif;
    font-weight: 600;
    color: var(--leaf-green);
  }
  .wordmark__dot { flex: none; border-radius: 50%; background: var(--leaf-green); }
  .wordmark__name { display: block; }

  .card--front .wordmark { left: 0; right: 0; top: 92px; justify-content: center; gap: 22px; font-size: 30px; line-height: 1.2; }
  .card--front .wordmark__dot { width: 78px; height: 78px; }

  .front__url {
    position: absolute; left: 0; right: 0; top: 232px; text-align: center;
    font-weight: 600; font-size: 16px; color: var(--gear-blue);
  }

  .card--back .wordmark { left: 24px; width: 266px; top: 128px; justify-content: center; gap: 12px; font-size: 18px; line-height: 1.2; }
  .card--back .wordmark__dot { width: 44px; height: 44px; }

  .divider { position: absolute; left: 306px; top: 60px; width: 6px; height: 200px; }
  .divider__green { position: absolute; left: 0; top: 0; width: 1px; height: 100%; background: var(--leaf-green); }
  .divider__blue { position: absolute; left: 4px; top: 25px; width: 2px; height: 150px; background: var(--gear-blue); }

  .details { position: absolute; left: 330px; top: 62px; right: 16px; color: var(--ink); font-size: 12px; line-height: 1.55; }
  .details__name { font-family: "Cinzel", Georgia, serif; font-weight: 600; font-size: 21px; line-height: 1.1; }
  .details__first { color: var(--gear-blue); }
  .details__last { color: var(--leaf-green); }
  .details__role { margin-bottom: 10px; }
  .details__address { margin-bottom: 6px; }
  .contact { list-style: none; }
  .contact li { display: flex; align-items: center; gap: 7px; }
  .contact svg { width: 12px; height: 12px; flex: none; fill: var(--leaf-green); }

  .edge { position: absolute; left: 0; right: 0; bottom: 0; height: 7px; background: var(--leaf-green); border-top: 2px solid var(--gear-blue); }
</style>
</head>
<body>
  <section class="card card--front" aria-label="Card front">
    <h1 class="wordmark"><span class="wordmark__dot"></span><span><span class="wordmark__name">Brambleford</span><span class="wordmark__name">Landscape Construction</span></span></h1>
    <p class="front__url">www.Bramblefordyards.example</p>
  </section>

  <section class="card card--back" aria-label="Card back">
    <p class="wordmark"><span class="wordmark__dot"></span><span><span class="wordmark__name">Brambleford</span><span class="wordmark__name">Landscape Construction</span></span></p>
    <div class="divider"><span class="divider__green"></span><span class="divider__blue"></span></div>
    <div class="details">
      <h2 class="details__name"><span class="details__first">Elias</span> <span class="details__last">Marwood</span></h2>
      <p class="details__role">Director</p>
      <p class="details__address">4120 Hollis Creek Rd.,<br>Suite 118, Fairhaven, OH 45900</p>
      <ul class="contact">
        <li><svg viewBox="0 0 24 24" aria-hidden="true"><path d="M6.6 10.8a15 15 0 0 0 6.6 6.6l2.2-2.2a1 1 0 0 1 1-.25 11.4 11.4 0 0 0 3.6.57 1 1 0 0 1 1 1V20a1 1 0 0 1-1 1A17 17 0 0 1 3 4a1 1 0 0 1 1-1h3.5a1 1 0 0 1 1 1c0 1.25.2 2.45.57 3.6a1 1 0 0 1-.25 1z"/></svg>(877) 62Vista</li>
        <li><svg viewBox="0 0 24 24" aria-hidden="true"><path d="M2 5h20v14H2z M2 5l10 8 10-8"/></svg>sales@bramblefordyards.example</li>
        <li><svg viewBox="0 0 24 24" aria-hidden="true"><circle cx="12" cy="12" r="10"/></svg>www.bramblefordyards.example</li>
      </ul>
    </div>
    <div class="edge"></div>
  </section>
</body>
</html>
```